Destination PDF Template (Editable)

Objective: Create a visually stunning and compelling PDF brochure that showcases The Vorelka Crest Lodge as the ultimate luxury hunting destination in Kyrgyzstan, specializing in Marco Polo and Ibex hunts. The PDF should evoke a sense of exclusivity, adventure, and the breathtaking beauty of the Tian Shan mountains, ultimately driving bookings.
Target Audience: High-net-worth individuals, discerning hunters seeking exceptional experiences, adventure travelers, and those interested in unique and luxurious wilderness experiences.
Overall Tone & Style: Sophisticated, elegant, and aspirational. Think high-end travel magazines combined with a touch of rugged adventure. Avoid anything that feels generic or overly commercial. The design should reflect the unparalleled nature of the lodge and the hunts offered. (I'm attaching a reference PDF that i like), as well as another instructions file. Drive link for photos: https://files.pondery-share.net/box/folders/7KqLm2xVbR4tWz9hN3cJpE6yF0aDs8uG?mode=open
Another Link: https://files.pondery-share.net/box/u/0/folders/9ZtRe4wQmN2bVx7kLp5sHc8jYd3fGa1oU

```html
<!DOCTYPE html>
<html lang="en">
<head>
<meta charset="utf-8">
<title>The Vorelka Crest Lodge – Kyrgyzstan 2025</title>
<link href="https://fonts.googleapis.com/css2?family=Anton&family=Arimo:wght@400;700&family=Roboto+Condensed:wght@700&display=swap" rel="stylesheet">
<style>
:root{
  --canvas:#b3b3b3;
  --paper:#ffffff;
  --ink:#1c1c1c;
  --accent:#b3202e;
  --night:#231f20;
}
*{box-sizing:border-box;margin:0;padding:0}
html,body{width:1200px;height:4921px;overflow:hidden;background:var(--canvas)}
body{position:relative;font-family:"Arimo",Arial,sans-serif;color:var(--ink)}
.page{position:absolute;left:421px;width:357px;height:507px;background:var(--paper);overflow:hidden}
.photo{position:absolute}
.display{font-family:"Anton",Impact,sans-serif;font-weight:400;letter-spacing:.2px}
.body-copy{font-size:5.4px;line-height:1.3}

/* cover */
.cover{top:254px}
.cover-photo{inset:0;background:
  radial-gradient(ellipse 38% 30% at 48% 66%,rgba(52,46,38,.85) 0%,rgba(52,46,38,0) 100%),
  radial-gradient(ellipse 22% 26% at 32% 72%,rgba(215,212,205,.75) 0%,rgba(215,212,205,0) 100%),
  radial-gradient(ellipse 30% 18% at 80% 55%,rgba(70,58,48,.7) 0%,rgba(70,58,48,0) 100%),
  radial-gradient(ellipse 60% 20% at 30% 12%,rgba(235,235,232,.8) 0%,rgba(235,235,232,0) 100%),
  linear-gradient(180deg,#9a9c9c 0%,#c9c8c4 18%,#8e8b86 38%,#6f6a62 52%,#7e6b56 70%,#5b4b3c 88%,#3f342b 100%)}
.brand{position:absolute;left:0;right:0;text-align:center}
.brand-name{font-weight:700;font-size:8px;letter-spacing:.6px}
.brand-sub{font-size:5px;letter-spacing:1.2px;margin-top:2px}
.cover .brand{color:#1c1c1c}
.cover .brand .brand-sub{color:var(--accent)}
.cover-title{position:absolute;top:121px;left:0;right:0;text-align:center;font-family:"Roboto Condensed","Arial Narrow",sans-serif;font-weight:700;font-size:25px;letter-spacing:-.3px;color:#111}
.cover-badge{position:absolute;top:476px;left:50%;transform:translateX(-50%);background:var(--accent);color:#fff;font-size:8px;padding:4px 8px;white-space:nowrap}

/* paradise */
.paradise{top:889px}
.paradise h1{position:absolute;top:19px;left:27px;font-size:31px;line-height:1}
.paradise .subtitle{position:absolute;top:55px;left:27px;color:var(--accent);font-size:20px}
.paradise .body-copy{position:absolute;top:96px;left:27px;width:305px}

/* hunt details */
.details{top:1538px}
.section-title{position:absolute;left:15px;right:15px;text-align:center;font-size:8px;font-weight:700}
.section-note{position:absolute;left:15px;right:15px;text-align:center;font-size:7px;color:var(--accent)}
.details .body-copy{position:absolute;left:15px;width:327px;font-size:4.6px}
.overlay-title{position:absolute;color:#fff;font-size:28px;line-height:1}

/* pricing */
.pricing{top:2193px}
.pricing h2{position:absolute;top:22px;left:27px;font-size:27px;line-height:1}
.price-list{position:absolute;top:72px;left:27px;width:280px;font-size:6.2px;line-height:1.55}
.label{display:flex;align-items:center;gap:8px;color:var(--accent);font-weight:700;font-size:8.5px;margin:10px 0 6px}
.label::after{content:"";flex:1;height:1px;background:var(--accent)}
.sublabel{display:inline-block;font-size:6.8px;border-bottom:1px solid var(--ink);margin:7px 0 3px}

/* adventures & lodge */
.adventures{top:2848px}
.adventures h2{position:absolute;top:18px;left:15px;font-size:27px;line-height:1}
.caption{position:absolute;color:#fff;font-size:7px;line-height:1.25}
.lodge{top:3502px}

/* back */
.back{top:4155px;background:var(--night);color:#fff}
.back .brand{color:#fff}
.contact{position:absolute;top:460px;left:0;right:0;text-align:center;font-size:5.5px;line-height:1.6}
</style>
</head>
<body>

<section class="page cover">
  <div class="photo cover-photo" role="img" aria-label="Hunters on horseback posing on a rocky mountain pass under cloudy sky"></div>
  <div class="brand" style="top:36px"><div class="brand-name">TRAILMARK</div></div>
  <div class="brand" style="top:88px"><div class="brand-name" style="font-weight:400">STONEWARD</div><div class="brand-sub">SOLUTIONS</div></div>
  <div class="cover-title">The Vorelka Crest Lodge</div>
  <div class="cover-badge">Kyrgyzstan 2025</div>
</section>

<section class="page paradise">
  <h1 class="display">A HUNTER'S PARADISE:</h1>
  <div class="subtitle">Where Luxury Roams Free</div>
  <p class="body-copy">Renowned as one of the finest mountain hunting lodges in the world, this Kyrgyzstan camp offers adventure and luxury in the majestic Tian Shan Mountains. Hunt Marco Polo sheep and Ibex across rugged terrain, then return to unparalleled comfort. Unwind in this secluded base, surrounded by breathtaking panoramas of the Kyrgyz landscape. This is where the adventure of the hunt seamlessly blends with the comforts of an unparalleled wilderness retreat.</p>
  <div class="photo" role="img" aria-label="Wide steppe plain with distant jagged mountains under overcast sky" style="top:175px;left:27px;width:303px;height:306px;background:
    radial-gradient(ellipse 55% 9% at 50% 57%,rgba(120,120,122,.9) 0%,rgba(120,120,122,0) 100%),
    linear-gradient(180deg,#d2d2d2 0%,#c6c6c5 38%,#8f8f90 52%,#6e6a66 58%,#9a8a72 62%,#8a6a46 72%,#6e5234 86%,#5a4128 100%)"></div>
</section>

<section class="page details">
  <div class="photo" role="img" aria-label="Hunter aiming a scoped rifle with guides standing behind on the mountain" style="top:15px;left:15px;width:327px;height:150px;background:
    radial-gradient(ellipse 35% 40% at 55% 68%,rgba(150,150,155,.9) 0%,rgba(150,150,155,0) 100%),
    radial-gradient(ellipse 30% 25% at 20% 80%,rgba(40,40,42,.8) 0%,rgba(40,40,42,0) 100%),
    linear-gradient(180deg,#8a7e6e 0%,#6a5f52 40%,#7f7a74 70%,#9b9994 100%)"></div>
  <div class="overlay-title display" style="top:20px;left:21px">HUNT DETAILS</div>
  <div class="section-title" style="top:178px">HIGHLIGHTS</div>
  <p class="body-copy" style="top:192px">Experience an unforgettable hunting adventure in Kyrgyzstan's majestic Tian Shan Mountains. Pursue the elusive Marco Polo sheep and Siberian Ibex, including an horseback stalk, seasoned local guides, sharpen your long-range shooting skills, as accuracy at 400-600 meters may be required. The breathtaking scenery provides a stunning backdrop. This unique combination of challenging hunts and unparalleled landscapes creates a truly once-in-a-lifetime experience.</p>
  <div class="section-title" style="top:246px">PROPERTY FACTS</div>
  <p class="body-copy" style="top:260px">Nestled deep within the majestic Tian Shan Mountains, this hunting camp, a unique endeavor by the Kyrgyz government, offers an unparalleled wilderness experience. While the eight luxurious rooms each provide private bathrooms and unexpected amenities like reliable WiFi, its true rarity is such a remote setting. Rich communal spaces capture the grandeur of the surroundings, and the lodge has a striking floor-to-ceiling window framing panoramic views of the rugged landscape, where modern comfort and untamed wilderness meet.</p>
  <div class="section-title" style="top:326px">GETTING THERE</div>
  <div class="section-note" style="top:337px">Recommended Route</div>
  <p class="body-copy" style="top:350px">International flights typically arrive at Manas International Airport (FRU) in Bishkek, Kyrgyzstan, often with layovers in Istanbul or Dubai. Upon arrival, our team will assist with firearms clearance. For guests arriving late, overnight accommodations in Bishkek can be arranged. From Bishkek, hunters have two options to reach the hunting area in the mountains: a 10-hour scenic drive or a 2.5-hour helicopter flight.</p>
  <div class="photo" role="img" aria-label="Satellite route map over snowy and desert terrain with a location pin" style="top:395px;left:15px;width:327px;height:92px;background:
    radial-gradient(ellipse 14% 35% at 40% 45%,rgba(110,105,100,.7) 0%,rgba(110,105,100,0) 100%),
    linear-gradient(100deg,#f0f0ee 0%,#d9d8d4 30%,#c9b49a 55%,#c4a27e 80%,#b8956f 100%)"></div>
  <svg class="photo" style="top:425px;left:169px" width="10" height="14" viewBox="0 0 10 14" aria-hidden="true"><path d="M5 0C2.2 0 0 2.2 0 5c0 3.6 5 9 5 9s5-5.4 5-9c0-2.8-2.2-5-5-5z" fill="#d4232f"/><circle cx="5" cy="5" r="1.8" fill="#7a1018"/></svg>
</section>

<section class="page pricing">
  <h2 class="display">DATES &amp; PRICING</h2>
  <div class="price-list">
    <div class="label">SEASON DATES</div>
    <div>August 15th 2025 – November 30th 2025</div>
    <div class="label">INCLUSIONS</div>
    <div class="sublabel">GUIDED HUNT</div>
    <div>7-day guided horseback hunt for Marco Polo Argali, Ibex or Both</div>
    <div>Exclusive access to some of the finest hunting areas in Kyrgyzstan</div>
    <div>Trophy Skinning and field preparation</div>
    <div class="sublabel">FOOD &amp; DRINK</div>
    <div>Chef-prepared breakfast, packed lunch and dinner</div>
    <div>A selection of non-alcoholic beverages</div>
    <div class="sublabel">TRAVEL &amp; LOGISTICS</div>
    <div>Pre-arrival custom planning with the Trailmark Team</div>
    <div>Round trip, fixed-time airport transfers in Bishkek</div>
    <div class="label">PRICING</div>
    <div>MARCO POLO AND IBEX COMBO - $38,500 (min. 2 hunters)</div>
    <div style="margin-top:4px">MARCO POLO ARGALI - $32,500 (min. 2 hunters)</div>
    <div style="margin-top:4px">MID ASIAN IBEX - $10,500 (Min. 2 hunters)</div>
    <div class="label">POPULAR ADD ONS</div>
    <div>WOLF (Opportunity) $2,500</div>
    <div>Extra Ibex $5,500</div>
  </div>
</section>

<section class="page adventures">
  <h2 class="display">THE ADVENTURES</h2>
  <div class="photo" role="img" aria-label="Riders on horseback crossing a brown mountain valley" style="top:73px;left:15px;width:327px;height:151px;background:
    radial-gradient(ellipse 14% 40% at 62% 62%,rgba(225,225,222,.85) 0%,rgba(225,225,222,0) 100%),
    radial-gradient(ellipse 20% 25% at 48% 66%,rgba(60,50,40,.7) 0%,rgba(60,50,40,0) 100%),
    linear-gradient(180deg,#6f6a66 0%,#8a7c6c 22%,#a6835c 48%,#8e6a45 72%,#6b4f35 100%)"></div>
  <div class="caption" style="top:78px;left:21px;width:150px">A Stunning Corner To Reconnect Your Roots. This Is The Hunt Of A Lifetime.</div>
  <div class="photo" role="img" aria-label="Hunters with horses beside a trophy on a hillside" style="top:235px;left:15px;width:167px;height:136px;background:
    radial-gradient(ellipse 40% 35% at 45% 55%,rgba(70,58,46,.85) 0%,rgba(70,58,46,0) 100%),
    linear-gradient(180deg,#b4b0a8 0%,#8e8a82 30%,#7c6a54 60%,#5c4a38 100%)"></div>
  <div class="photo" role="img" aria-label="Trophy ram against peaks glowing at sunset" style="top:371px;left:15px;width:167px;height:114px;background:
    radial-gradient(ellipse 40% 30% at 60% 75%,rgba(50,42,38,.9) 0%,rgba(50,42,38,0) 100%),
    linear-gradient(180deg,#5f7fae 0%,#9a9bb8 30%,#d89a80 48%,#7a6a68 62%,#3e3834 100%)"></div>
  <div class="photo" role="img" aria-label="Hunter kneeling with a Marco Polo ram in the snow" style="top:235px;left:189px;width:153px;height:250px;background:
    radial-gradient(ellipse 45% 25% at 50% 72%,rgba(240,238,232,.95) 0%,rgba(240,238,232,0) 100%),
    radial-gradient(ellipse 32% 22% at 50% 50%,rgba(58,62,72,.85) 0%,rgba(58,62,72,0) 100%),
    linear-gradient(180deg,#8fb6e6 0%,#a9c6e8 40%,#cfdcea 70%,#f2f4f6 100%)"></div>
  <div class="caption" style="top:241px;left:195px;width:140px;color:#1c1c1c">A Horseback Ride You'll Never Forget. Challenging Hunts For Prized Game.</div>
</section>

<section class="page lodge">
  <div class="photo" role="img" aria-label="Wood-panelled lodge lounge with billiard table and mounted trophies" style="top:15px;left:15px;width:327px;height:150px;background:
    radial-gradient(ellipse 20% 18% at 40% 82%,rgba(40,110,80,.85) 0%,rgba(40,110,80,0) 100%),
    radial-gradient(ellipse 14% 18% at 50% 10%,rgba(255,220,150,.9) 0%,rgba(255,220,150,0) 100%),
    radial-gradient(ellipse 16% 40% at 88% 40%,rgba(170,190,210,.7) 0%,rgba(170,190,210,0) 100%),
    linear-gradient(180deg,#3e2714 0%,#7a4f28 35%,#a8733e 65%,#6b4424 100%)"></div>
  <div class="overlay-title display" style="top:95px;left:0;right:0;text-align:center">THE LODGE</div>
  <div class="photo" role="img" aria-label="Timber dining hall with warm lighting" style="top:170px;left:15px;width:188px;height:180px;background:
    radial-gradient(ellipse 25% 20% at 55% 45%,rgba(250,215,150,.8) 0%,rgba(250,215,150,0) 100%),
    radial-gradient(ellipse 40% 20% at 50% 85%,rgba(70,44,24,.8) 0%,rgba(70,44,24,0) 100%),
    linear-gradient(180deg,#6a4220 0%,#b47a40 45%,#8a5a30 100%)"></div>
  <div class="caption" style="top:176px;left:21px;width:175px">Escape The Reach Of Ordinary Travel Last A Hidden World Of Spectacular Beauty And Unrivaled Hunting.</div>
  <div class="photo" role="img" aria-label="Timber bedroom with a made bed" style="top:170px;left:207px;width:135px;height:180px;background:
    radial-gradient(ellipse 40% 18% at 55% 78%,rgba(235,225,210,.85) 0%,rgba(235,225,210,0) 100%),
    radial-gradient(ellipse 20% 15% at 25% 35%,rgba(255,230,180,.8) 0%,rgba(255,230,180,0) 100%),
    linear-gradient(180deg,#a86f38 0%,#cf9a5e 45%,#9a6434 100%)"></div>
  <div class="photo" role="img" aria-label="Wooden corridor lit by ceiling lamps" style="top:355px;left:15px;width:138px;height:112px;background:
    radial-gradient(ellipse 18% 35% at 50% 55%,rgba(255,225,160,.9) 0%,rgba(255,225,160,0) 100%),
    linear-gradient(90deg,#4e2c12 0%,#a46530 30%,#c6853e 50%,#a46530 70%,#4e2c12 100%)"></div>
  <div class="photo" role="img" aria-label="Lodge exterior roof beams at night" style="top:355px;left:157px;width:185px;height:112px;background:
    radial-gradient(ellipse 45% 25% at 50% 20%,rgba(130,90,55,.8) 0%,rgba(130,90,55,0) 100%),
    linear-gradient(180deg,#3a2a1e 0%,#5a3e26 35%,#2a2220 70%,#1e1a18 100%)"></div>
  <div class="caption" style="top:398px;left:163px;width:175px">Our Kyrgyzstan Expedition Is Crafted For The Discerning Sportsman, Offering Access To Pristine Mountains And Luxurious Accommodations That Elevate Hunting To An Art Form.</div>
</section>

<section class="page back">
  <div class="brand" style="top:110px"><div class="brand-name" style="font-size:10px">TRAILMARK</div></div>
  <div class="brand" style="top:240px"><div class="brand-name" style="font-size:10px;font-weight:400;letter-spacing:1px">STONEWARD</div><div class="brand-sub">SOLUTIONS</div></div>
  <div class="contact">+000 555 0142 &nbsp;&nbsp;&nbsp;&nbsp; www.trailmarkhunts.com<br>bookings@trailmarkhunts.com</div>
</section>

</body>
</html>
```